Larkfield Ridge Management

I need a professional website. My current website is larkfieldridgemanagement.com and I hate it. It was created with some AI tool very quickly because I needed a site up and running with no advanced notice. I’m open to all designs .. I trust you, the professionals will deliver the results I’m anxiously awaiting! :)

```html
<!DOCTYPE html>
<html lang="en">
<head>
<meta charset="utf-8">
<title>Larkfield Ridge Management</title>
<link href="https://fonts.googleapis.com/css2?family=Poppins:wght@300;400;500;600;700&display=swap" rel="stylesheet">
<style>
:root{
  --navy:#123d78;
  --blue:#1c4f97;
  --red:#d1242c;
  --ink:#1f2a37;
  --muted:#5a5f66;
  --light:#efeff0;
  --footer:#1d1d1f;
  --gold:#f4b23a;
  --white:#ffffff;
}
*{margin:0;padding:0;box-sizing:border-box}
html,body{width:1200px;height:3678px;overflow:hidden}
body{font-family:'Poppins',sans-serif;color:var(--ink);background:var(--white);position:relative}
.abs{position:absolute}
.btn{position:absolute;background:var(--red);color:var(--white);border-radius:20px;font-size:11.5px;font-weight:600;text-transform:uppercase;display:flex;align-items:center;justify-content:center;letter-spacing:.2px}
.section-title{position:absolute;left:0;width:1200px;text-align:center;font-size:33px;font-weight:600;text-transform:uppercase;color:var(--ink)}

/* hero */
.hero{left:0;top:0;width:1200px;height:870px;background:linear-gradient(180deg,#1b3a66 0%,#2b3f5a 30%,#6a5448 55%,#b86a35 75%,#3a3c48 100%)}
.hero-curve{left:0;top:700px}
.header-band{left:0;top:0;width:1200px;height:126px;background:var(--navy)}
.topbar{left:161px;top:0;width:878px;height:36px;background:var(--red);border-radius:0 0 8px 8px;color:var(--white);font-size:12.5px}
.topbar .social{position:absolute;top:11px;width:14px;height:14px;border:1.5px solid var(--white);border-radius:50%}
.topbar .contact{position:absolute;top:9px;display:flex;align-items:center;gap:8px}
.brand{left:161px;top:50px;width:110px;height:100px;display:flex;align-items:center;gap:8px;color:var(--white);font-weight:700;font-size:17px;line-height:1.1}
.brand .mark{width:18px;height:18px;border-radius:50%;background:var(--red);flex:none}
.nav{top:72px;color:var(--white);font-size:14px}
.nav.active{font-weight:600}
.hero-title{left:0;top:320px;width:1200px;text-align:center;color:var(--white);font-size:49px;font-weight:500;line-height:58px;text-transform:uppercase}
.hero-sub{left:0;top:447px;width:1200px;text-align:center;color:var(--white);font-size:15px}
.hero-arrow{top:432px}

/* feature cards */
.feature{position:absolute;width:278px;height:133px;border-radius:10px;overflow:hidden;box-shadow:0 10px 24px rgba(0,0,0,.2)}
.feature.blue{background:var(--blue)}
.feature.red{background:var(--red)}
.feature .photo{position:absolute;right:0;top:0;width:150px;height:133px}
.feature h3{position:absolute;left:17px;top:28px;color:var(--white);font-size:18px;font-weight:600;line-height:23px;z-index:2}

/* about */
.about-title{left:161px;top:1003px;font-size:33px;font-weight:600}
.about-text{left:161px;top:1059px;width:364px;font-size:13.3px;line-height:19.6px;color:var(--muted)}
.about-photo{left:600px;top:990px;width:439px;height:394px;border-radius:12px;background:linear-gradient(135deg,#d9d6d0,#8a7a6a 50%,#4a4b52)}

/* services */
.services-bg{left:0;top:1460px;width:1200px;height:484px;background:var(--light)}
.service-photo{position:absolute;top:1600px;width:277px;height:179px;border-radius:6px}
.service-name{position:absolute;top:1796px;font-size:18px;font-weight:500}
.service-text{position:absolute;top:1833px;width:230px;font-size:12.5px;line-height:15.5px;color:var(--muted)}

/* testimonials */
.testi-bg{left:0;top:1944px;width:1200px;height:478px;background:linear-gradient(160deg,#1d4f95,#174280 60%,#22508d)}
.testi-card{position:absolute;background:var(--white);border-radius:4px;padding:22px 26px}
.testi-card.side{background:rgba(255,255,255,.78)}
.stars{color:var(--gold);font-size:16px;letter-spacing:2px}
.stars span{color:var(--ink);font-size:13px;letter-spacing:0;margin-left:4px;font-weight:500}
.testi-text{font-size:12.3px;line-height:19px;color:var(--muted);margin-top:8px}
.author{display:flex;align-items:center;gap:18px;margin-top:16px}
.avatar{width:54px;height:54px;border-radius:50%;background:#c9ccd2;flex:none}
.author .name{font-size:15px;color:var(--muted)}
.author .co{font-size:14.5px;font-weight:600;color:var(--ink)}
.quote{position:absolute;font-size:90px;font-weight:700;color:#4f7fbf;line-height:1}
.dot-btn{position:absolute;top:2344px;width:34px;height:34px;border-radius:50%;background:var(--red)}

/* news */
.news-photo{position:absolute;top:2574px;width:277px;height:215px;border-radius:6px}
.news-date{position:absolute;top:2711px;width:44px;height:68px;background:var(--red);border-radius:4px;color:var(--white);text-align:center;line-height:1}
.news-date b{display:block;font-size:25px;font-weight:600;margin-top:8px}
.news-date small{font-size:13px;font-weight:600}
.news-title{position:absolute;top:2810px;width:260px;font-size:15px;font-weight:500;line-height:19px}
.news-text{position:absolute;top:2858px;width:280px;font-size:11.4px;line-height:14.5px;color:var(--muted)}
.news-more{position:absolute;top:2902px;font-size:11.5px;font-style:italic;display:flex;align-items:center;gap:8px}

/* subscribe */
.subscribe-bg{left:0;top:3061px;width:1200px;height:196px;background:#f3f3f4}
.subscribe-title{left:159px;top:3120px;font-size:34px;font-weight:600;line-height:39px}
.email-field{left:524px;top:3152px;width:335px;height:38px;border-bottom:1.5px solid #8a8d93;display:flex;align-items:center;gap:14px;font-size:14px;color:var(--ink);padding-left:2px}

/* footer */
.footer{left:0;top:3257px;width:1200px;height:421px;background:var(--footer);color:var(--white)}
.footer-brand{left:0;top:3320px;width:1200px;display:flex;justify-content:center;align-items:center;gap:10px;color:var(--white);font-size:22px;font-weight:700}
.footer-brand .mark{width:20px;height:20px;border-radius:50%;background:var(--red)}
.f-col{position:absolute;top:3428px;color:var(--white)}
.f-col h4{font-size:17px;font-weight:500;padding-bottom:4px;border-bottom:2px solid var(--white);display:inline-block;margin-bottom:20px;color:var(--white)}
.f-col li{list-style:none;font-size:13.5px;height:37.5px;color:var(--white)}
.f-contact li{display:flex;align-items:center;gap:10px;height:37.5px}
.f-icon{width:26px;height:26px;border-radius:50%;background:var(--white);display:flex;align-items:center;justify-content:center;flex:none}
.f-social{position:absolute;top:3594px;width:32px;height:32px;border-radius:50%;border:2px solid var(--white)}
</style>
</head>
<body>

<!-- hero -->
<div class="abs hero" role="img" aria-label="City skyline at dusk with tall towers"></div>
<svg class="abs hero-curve" width="1200" height="180" viewBox="0 0 1200 180"><path d="M0,64 Q600,250 1200,64 L1200,180 L0,180 Z" fill="#ffffff"/></svg>
<div class="abs header-band"></div>

<div class="abs topbar">
  <div class="social" style="left:28px"></div>
  <div class="social" style="left:62px"></div>
  <div class="social" style="left:101px"></div>
  <div class="contact" style="left:468px">
    <svg width="13" height="13" viewBox="0 0 24 24"><path fill="#fff" d="M6.6 10.8a15.1 15.1 0 0 0 6.6 6.6l2.2-2.2c.3-.3.7-.4 1-.2 1.1.4 2.3.6 3.6.6.6 0 1 .4 1 1V20c0 .6-.4 1-1 1A17 17 0 0 1 3 4c0-.6.4-1 1-1h3.5c.6 0 1 .4 1 1 0 1.3.2 2.5.6 3.6.1.3 0 .7-.2 1z"/></svg>
    614-555-0182
  </div>
  <div class="contact" style="left:609px">
    <svg width="14" height="11" viewBox="0 0 24 18"><rect x="1" y="1" width="22" height="16" rx="1" fill="none" stroke="#fff" stroke-width="2"/><path d="M1 1l11 9 11-9" fill="none" stroke="#fff" stroke-width="2"/></svg>
    info@larkfieldridgemanagement.com
  </div>
</div>

<div class="abs brand"><span class="mark"></span>Larkfield Ridge</div>

<div class="abs nav active" style="left:419px">Home</div>
<div class="abs nav" style="left:499px">About Us</div>
<div class="abs nav" style="left:602px">Services</div>
<div class="abs nav" style="left:701px">News</div>
<div class="abs nav" style="left:780px">Contact Us</div>
<div class="btn" style="left:876px;top:61px;width:163px;height:42px;border-radius:21px">Book Consultation</div>

<div class="abs hero-title">Professional Property<br>Management You Can Trust</div>
<div class="abs hero-sub">A true partner, not just a vendor.</div>
<div class="btn" style="left:531px;top:487px;width:138px;height:36px">Learn More</div>
<svg class="abs hero-arrow" style="left:28px" width="16" height="26" viewBox="0 0 16 26"><path d="M13 2L3 13l10 11" fill="none" stroke="#fff" stroke-width="2"/></svg>
<svg class="abs hero-arrow" style="left:1156px" width="16" height="26" viewBox="0 0 16 26"><path d="M3 2l10 11L3 24" fill="none" stroke="#fff" stroke-width="2"/></svg>

<!-- feature cards -->
<div class="feature blue" style="left:161px;top:721px">
  <div class="photo" role="img" aria-label="Modern two-storey residential house" style="background:linear-gradient(90deg,rgba(28,79,151,1),#8a7560 40%,#e8e2d8)"></div>
  <h3>Residential<br>Property</h3>
</div>
<div class="feature red" style="left:461px;top:767px">
  <div class="photo" role="img" aria-label="Modern commercial apartment building" style="background:linear-gradient(90deg,rgba(209,36,44,1),#6d7ea8 40%,#c9c4b8)"></div>
  <h3>Commercial<br>Property</h3>
</div>
<div class="feature blue" style="left:761px;top:721px">
  <div class="photo" role="img" aria-label="Hands reviewing documents and charts on a desk" style="background:linear-gradient(90deg,rgba(28,79,151,1),#9aa6b6 40%,#e6e2dc)"></div>
  <h3>Tenant<br>Placement</h3>
</div>

<!-- about -->
<h2 class="abs about-title">ABOUT US</h2>
<p class="abs about-text">Lorem Ipsum is simply dummy text of the printing and typesetting industry. Lorem Ipsum has been the industry's standard dummy text ever since the 1500s, when an unknown printer took a galley of type and scrambled it to make a type specimen book. It has survived not only five centuries, but also the leap into electronic typesetting, remaining essentially unchanged. It was popularised in the 1960s with the release of Letraset sheets containing Lorem Ipsum passages, and more recently with desktop publishing software like Aldus PageMaker including versions of Lorem Ipsum.</p>
<div class="btn" style="left:161px;top:1324px;width:136px;height:37px">Learn More</div>
<div class="abs about-photo" role="img" aria-label="Two colleagues reviewing documents together in an office"></div>

<!-- services -->
<div class="abs services-bg"></div>
<h2 class="section-title" style="top:1515px">Our Services</h2>
<div class="service-photo" style="left:161px;background:linear-gradient(160deg,#8fb0d4,#c9c9c4 55%,#5d4a3a)" role="img" aria-label="White family house with blue roof"></div>
<div class="service-photo" style="left:462px;background:linear-gradient(160deg,#3f7fb8,#b88a5c 55%,#6e5238)" role="img" aria-label="Modern commercial tower with terraces"></div>
<div class="btn" style="left:524px;top:1670px;width:153px;height:38px">Learn More</div>
<div class="service-photo" style="left:763px;background:linear-gradient(160deg,#d8cfc0,#7a8798 55%,#e4e0da)" role="img" aria-label="Agent meeting with tenants in a living room"></div>
<div class="service-name" style="left:161px">Residential Property</div>
<div class="service-name" style="left:461px">Commercial Property</div>
<div class="service-name" style="left:763px">Tenant Placement</div>
<p class="service-text" style="left:161px">It is a long established fact that a reader will be distracted by th looking at its layout.</p>
<p class="service-text" style="left:462px">It is a long established fact that a reader will be distracted by th looking at its layout.</p>
<p class="service-text" style="left:763px">It is a long established fact that a reader will be distracted by th looking at its layout.</p>

<!-- testimonials -->
<div class="abs testi-bg"></div>
<h2 class="section-title" style="top:1994px;color:var(--white)">Client Testimonial</h2>

<div class="testi-card side" style="left:-200px;top:2094px;width:513px;height:206px">
  <div class="stars">★★★★★<span>5.0</span></div>
  <p class="testi-text">There are many variations of passages of Lorem Ipsum available, but the majority have suffered alteration in some form, by injected humour, you need to be sure there isn't anything embarrassing hidden in the middle of text. All the tend to repeat predefined chunks as necess.</p>
  <div class="author"><div class="avatar"></div><div><div class="name">Dana Whitfield</div><div class="co">Harlow Bay Holdings Ltd.</div></div></div>
  <div class="quote" style="right:24px;bottom:-10px">“</div>
</div>

<div class="testi-card" style="left:343px;top:2079px;width:514px;height:207px">
  <div class="stars">★★★★★<span>5.0</span></div>
  <p class="testi-text">There are many variations of passages of Lorem Ipsum available, but the majority have suffered alteration in some form, by injected humour, you need to be sure there isn't anything embarrassing hidden in the middle of text. All the tend to repeat predefined chunks as necess.</p>
  <div class="author"><div class="avatar"></div><div><div class="name">Dana Whitfield</div><div class="co">Harlow Bay Holdings Ltd.</div></div></div>
  <div class="quote" style="right:24px;bottom:-10px">“</div>
</div>

<div class="testi-card side" style="left:889px;top:2094px;width:513px;height:206px">
  <div class="stars">★★★★★<span>5.0</span></div>
  <p class="testi-text">There are many variations of passages of Lorem Ipsum available, but the majority have suffered alteration in some form, by injected humour, you need to be sure there isn't anything embarrassing hidden in the middle of text. All the tend to repeat predefined chunks as necess.</p>
  <div class="author"><div class="avatar"></div><div><div class="name">Dana Whitfield</div><div class="co">Harlow Bay Holdings Ltd.</div></div></div>
</div>

<div class="dot-btn" style="left:557px"><svg width="34" height="34" viewBox="0 0 34 34"><path d="M23 17H11m5-5l-5 5 5 5" fill="none" stroke="#fff" stroke-width="1.6"/></svg></div>
<div class="dot-btn" style="left:607px"><svg width="34" height="34" viewBox="0 0 34 34"><path d="M11 17h12m-5-5l5 5-5 5" fill="none" stroke="#fff" stroke-width="1.6"/></svg></div>

<!-- news -->
<h2 class="section-title" style="top:2487px">Latest News</h2>
<div class="news-photo" style="left:161px;background:linear-gradient(160deg,#6fa6dc,#c7c4bc 55%,#5e7d4a)" role="img" aria-label="Modern apartment blocks under blue sky"></div>
<div class="news-photo" style="left:462px;background:linear-gradient(160deg,#c7b48a,#b46a3a 55%,#4d5a2c)" role="img" aria-label="Miniature house model on a table"></div>
<div class="news-photo" style="left:761px;background:linear-gradient(160deg,#58636e,#2e3440 50%,#6c8a4a)" role="img" aria-label="Agent shaking hands with a client outside a home"></div>
<div class="news-date" style="left:169px"><b>10</b><small>FEB</small></div>
<div class="news-date" style="left:470px"><b>10</b><small>FEB</small></div>
<div class="news-date" style="left:769px"><b>10</b><small>FEB</small></div>
<div class="news-title" style="left:161px">When To Seek Business For Your Advisory Support</div>
<div class="news-title" style="left:462px">When To Seek Business For Your Advisory Support</div>
<div class="news-title" style="left:761px">When To Seek Business For Your Advisory Support</div>
<p class="news-text" style="left:161px">It is a long established fact that a reader will be distracted by the looking at its layout.</p>
<p class="news-text" style="left:462px">It is a long established fact that a reader will be distracted by the looking at its layout.</p>
<p class="news-text" style="left:761px">It is a long established fact that a reader will be distracted by the looking at its layout.</p>
<div class="news-more" style="left:163px">LEARN MORE <svg width="14" height="10" viewBox="0 0 14 10"><path d="M0 5h12M8 1l4 4-4 4" fill="none" stroke="#1f2a37" stroke-width="1.2"/></svg></div>
<div class="news-more" style="left:464px">LEARN MORE <svg width="14" height="10" viewBox="0 0 14 10"><path d="M0 5h12M8 1l4 4-4 4" fill="none" stroke="#1f2a37" stroke-width="1.2"/></svg></div>
<div class="news-more" style="left:764px">LEARN MORE <svg width="14" height="10" viewBox="0 0 14 10"><path d="M0 5h12M8 1l4 4-4 4" fill="none" stroke="#1f2a37" stroke-width="1.2"/></svg></div>
<div class="btn" style="left:526px;top:2964px;width:148px;height:36px">View All Blog</div>

<!-- subscribe -->
<div class="abs subscribe-bg"></div>
<h2 class="abs subscribe-title">Subscribe for the<br>Exclusive Updates!</h2>
<div class="abs email-field">
  <svg width="22" height="16" viewBox="0 0 24 18"><rect x="1" y="1" width="22" height="16" rx="1" fill="none" stroke="#1f2a37" stroke-width="2"/><path d="M1 1l11 9 11-9" fill="none" stroke="#1f2a37" stroke-width="2"/></svg>
  Enter Email Address
</div>
<div class="btn" style="left:889px;top:3146px;width:150px;height:35px">Subscribe</div>

<!-- footer -->
<div class="abs footer"></div>
<div class="abs footer-brand"><span class="mark"></span>Larkfield Ridge</div>

<div class="f-col" style="left:161px">
  <h4>Working Hours</h4>
  <ul><li>Mon-Fri: 9am - 6pm</li><li>Saturday: 9am - 4pm</li><li>Sunday: Closed</li></ul>
</div>
<div class="f-social" style="left:161px"></div>
<div class="f-social" style="left:204px"></div>
<div class="f-social" style="left:247px"></div>

<div class="f-col" style="left:398px">
  <h4>Quick Links</h4>
  <ul><li>Home</li><li>About Us</li><li>Services</li><li>Contact Us</li></ul>
</div>
<div class="f-col" style="left:574px">
  <h4>Services</h4>
  <ul><li>Residential Property</li><li>Commercial Property</li><li>Tenant Placement</li><li>Maintenance Coordination</li></ul>
</div>
<div class="f-col f-contact" style="left:817px">
  <h4>Contact Us</h4>
  <ul>
    <li><span class="f-icon"><svg width="13" height="13" viewBox="0 0 24 24"><path fill="#1d1d1f" d="M6.6 10.8a15.1 15.1 0 0 0 6.6 6.6l2.2-2.2c.3-.3.7-.4 1-.2 1.1.4 2.3.6 3.6.6.6 0 1 .4 1 1V20c0 .6-.4 1-1 1A17 17 0 0 1 3 4c0-.6.4-1 1-1h3.5c.6 0 1 .4 1 1 0 1.3.2 2.5.6 3.6.1.3 0 .7-.2 1z"/></svg></span>614-555-0182</li>
    <li><span class="f-icon"><svg width="13" height="10" viewBox="0 0 24 18"><rect x="1" y="1" width="22" height="16" rx="1" fill="none" stroke="#1d1d1f" stroke-width="2.5"/><path d="M1 1l11 9 11-9" fill="none" stroke="#1d1d1f" stroke-width="2.5"/></svg></span>info@larkfieldridgemanagement.com</li>
    <li><span class="f-icon"><svg width="12" height="14" viewBox="0 0 24 28"><path fill="#1d1d1f" d="M12 0a10 10 0 0 0-10 10c0 7 10 18 10 18s10-11 10-18A10 10 0 0 0 12 0zm0 14a4 4 0 1 1 0-8 4 4 0 0 1 0 8z"/></svg></span>122, Lorem ipsum dolird</li>
  </ul>
</div>

</body>
</html>
```